Business Card Design For Office Furniture Clearance Company

Kestrel Office Clearance - our company name pretty much explains what we do, we clear offices for high end clients, mainly plc's and large international companies.

We require a nice looking business card that displays professionalism but without being too serious.

It would be nice to see just a little more than a conventional boring business card, make sure you add some flare.

Industry/Entity Type

Office Furniture

Contact Information for Business Card

CARD 1

Mark Holloway
Director
mark@kestrelofficeclearance.co.uk
m: 07700 153928

t: 01632 960418
www.kestrelofficeclearance.co.uk

Kestrel Office Clearance
Unit K4 B
2-8 Fenwick Lane
Ashcombe
Harwell Vale
ZZ9 4QT

free office clearances… you cant get better than that.

CARD 2

Peter Radford
Director
peter@kestrelofficeclearance.co.uk
m: 07700 382615

t: 01632 960418

Kestrel Office Clearance
Unit K4 B
2-8 Fenwick Lane
Ashcombe
Harwell Vale
ZZ9 4QT

Font styles to use
Sans Serif

Requirements
Must have
• A white background - as we have a blue logo.
Nice to have
• Nice use of the logo - play around with this and dissect it.

```html
<!DOCTYPE html>
<html lang="en">
<head>
<meta charset="utf-8">
<title>Kestrel Office Clearance – Business Card</title>
<link rel="stylesheet" href="https://fonts.googleapis.com/css2?family=Arimo:wght@400;700&display=swap">
<style>
  :root {
    --backdrop: #2b2b2d;
    --card-white: #ffffff;
    --card-mist: #e4e6e8;
    --brand-blue: #1a72b8;
    --brand-blue-light: #3f97d6;
    --brand-blue-deep: #0f5a97;
    --ink-grey: #6b6f73;
    --on-blue: #ffffff;
  }
  * { box-sizing: border-box; margin: 0; padding: 0; }
  html, body {
    width: 1200px; height: 997px; overflow: hidden;
    background: var(--backdrop);
    font-family: "Arimo", Arial, sans-serif;
  }
  .canvas { position: relative; width: 1200px; height: 997px; }
  .card {
    position: absolute; width: 580px; height: 368px;
    border-radius: 22px; overflow: hidden;
    background: linear-gradient(160deg, var(--card-white) 30%, var(--card-mist) 100%);
    box-shadow: 0 18px 40px rgba(0,0,0,0.55);
  }
  .card--front { left: 310px; top: 90px; }
  .card--back  { left: 310px; top: 530px; }
  .card > svg { position: absolute; inset: 0; width: 580px; height: 368px; }

  .brand-name {
    position: absolute; color: var(--brand-blue);
    font-weight: 700; font-size: 15px; letter-spacing: 0.2px; white-space: nowrap;
  }
  .card--front .brand-name { right: 150px; top: 52px; }
  .card--back .brand-name { left: 184px; top: 276px; color: var(--on-blue); }

  .person { position: absolute; left: 40px; top: 118px; }
  .person__name { color: var(--brand-blue-light); font-weight: 700; font-size: 28px; }
  .person__role { color: var(--ink-grey); font-size: 15px; margin-top: 2px; }

  .contacts {
    position: absolute; left: 40px; top: 226px; list-style: none;
    color: var(--on-blue); font-size: 15px; line-height: 22px;
  }
  .contacts li { display: flex; align-items: flex-start; gap: 10px; }
  .contacts svg { width: 14px; height: 14px; margin-top: 4px; flex: none; }

  .offer {
    position: absolute; left: 20px; right: 20px; top: 44px;
    text-align: center; color: var(--brand-blue); font-size: 16px; line-height: 26px;
    white-space: nowrap;
  }
  .site { position: absolute; right: 24px; top: 312px; text-align: right; color: var(--on-blue); }
  .site__url { font-size: 20px; letter-spacing: 0.3px; }
  .site__tagline { font-size: 11px; margin-top: 3px; }
</style>
</head>
<body>
<main class="canvas">

  <section class="card card--front" aria-label="Business card front">
    <svg viewBox="0 0 580 368" aria-hidden="true">
      <path d="M0,196 C160,188 300,168 420,110 C480,82 530,70 580,64 L580,368 L0,368 Z" fill="var(--brand-blue-light)"/>
      <path d="M0,214 C160,206 310,186 430,126 C490,98 535,88 580,84 L580,368 L0,368 Z" fill="var(--brand-blue)"/>
      <circle cx="492" cy="78" r="44" fill="var(--brand-blue)" stroke="var(--card-white)" stroke-width="4"/>
    </svg>
    <div class="brand-name">Kestrel Office Clearance</div>
    <div class="person">
      <div class="person__name">Mark Holloway</div>
      <div class="person__role">Director</div>
    </div>
    <ul class="contacts">
      <li>
        <svg viewBox="0 0 14 14" aria-hidden="true"><rect x="3" y="0.5" width="8" height="13" rx="1.5" fill="none" stroke="currentColor" stroke-width="1.4"/><circle cx="7" cy="11" r="0.9" fill="currentColor"/></svg>
        <span>07700 153928</span>
      </li>
      <li>
        <svg viewBox="0 0 14 14" aria-hidden="true"><path d="M3,1 L5.5,1 L6.5,4 L5,5.5 C6,7.5 7,8.5 8.5,9 L10,7.5 L13,8.5 L13,11 C13,12 12,13 11,13 C6,12.5 1.5,8 1,3 C1,2 2,1 3,1 Z" fill="currentColor"/></svg>
        <span>01632 960418</span>
      </li>
      <li>
        <svg viewBox="0 0 14 14" aria-hidden="true"><rect x="0.7" y="2.5" width="12.6" height="9" rx="1" fill="none" stroke="currentColor" stroke-width="1.4"/><path d="M1,3 L7,8 L13,3" fill="none" stroke="currentColor" stroke-width="1.4"/></svg>
        <span>mark@kestrelofficeclearance.co.uk</span>
      </li>
      <li>
        <svg viewBox="0 0 14 14" aria-hidden="true"><path d="M7,13.5 C4,9.5 2.5,7 2.5,5 A4.5,4.5 0 0 1 11.5,5 C11.5,7 10,9.5 7,13.5 Z" fill="currentColor"/><circle cx="7" cy="5" r="1.6" fill="var(--brand-blue)"/></svg>
        <span>Unit K4 B, 2-8 Fenwick Lane, Ashcombe, Harwell Vale<br>ZZ9 4QT</span>
      </li>
    </ul>
  </section>

  <section class="card card--back" aria-label="Business card back">
    <svg viewBox="0 0 580 368" aria-hidden="true">
      <path d="M0,244 C150,214 300,168 450,158 C515,154 555,166 580,176 L580,368 L0,368 Z" fill="var(--brand-blue-light)"/>
      <path d="M0,262 C160,232 310,190 455,182 C518,179 556,190 580,198 L580,368 L0,368 Z" fill="var(--brand-blue)"/>
      <path d="M0,322 C160,300 320,296 580,300 L580,368 L0,368 Z" fill="var(--brand-blue-deep)" opacity="0.35"/>
      <circle cx="118" cy="268" r="54" fill="var(--brand-blue)" stroke="var(--card-white)" stroke-width="5"/>
    </svg>
    <p class="offer">We offer FREE office furniture &amp; IT clearances anywhere in the UK.<br>No matter how small or large your office is, call us today to<br>book a free furniture consultation &amp; survey.</p>
    <div class="brand-name">Kestrel Office Clearance</div>
    <div class="site">
      <div class="site__url">www.kestrelofficeclearance.co.uk</div>
      <div class="site__tagline">Free Office Clearances… simply the easiest way to move</div>
    </div>
  </section>

</main>
</body>
</html>
```